Fin-Tech Firm Captivating Business Card Design

We need a logo design as well to compliment this business card.

We are a new startup based in Singapore called 'Brevora Technologies'.

We develop an array of financial solutions ranging from payment convenience to forex trading and remittance.

Our initial product is Pim - an application which allows user to pre-order food items which would be ready for pickup upon arrival.

We would like to see designs being in black and silver or whatever that looks appealing and exudes a fun and professional feel.

We're not picky as long as it doesn't look like common business cards will do.

I do have a current logo which i do not really like. It will be attached for reference sake

Info:

Brevora Technologies Pte. Ltd.
Company Registration no. 201678213K

FILE TO BE IN .AI and .PSD

Target Market(s)

-F&B (Online-Ordering)
-Finance(P2P Lending and Forex)

Industry/Entity Type

Finance

Contact Information for Business Card

Name
Position
Contact
Email
Address: 47 Merrow Street, Calder House, #14-03 Singapore 068215

Adrian Teo
Founder, Managing Director
+65 98471360
adrian.t@brevoratech.com

Kai Loh
Founder, Executive Director
+65 96603847
kai.l@brevoratech.com

Logo Text

Brevora Technologies

Font styles to use
Sans Serif

Requirements
Must have
• Something that has word play about link brev
• Minimalistic but also something that catches The Eye
• Gold/silver on white/black might be nice
• Animal logo ; horse, eagle, bull or bear
Nice to have
• Just make it look fun and cute
• Just a suggestion to make the Y of brevora stand out
Should not have
• Any landmarks of singapore
• Exclude Pte. Ltd.

```html
<!DOCTYPE html>
<html lang="en">
<head>
<meta charset="utf-8">
<title>Brevora Technologies – Business Card</title>
<link rel="stylesheet" href="https://fonts.googleapis.com/css2?family=Open+Sans:wght@400;600&display=swap">
<style>
  :root {
    --backdrop: #000000;
    --card-white: #f2f2f2;
    --brand-orange: #f0a81c;
    --text-dark: #1e1e1e;
    --mark-white: #ffffff;
  }
  * { margin: 0; padding: 0; box-sizing: border-box; }
  html, body {
    width: 1200px; height: 900px; overflow: hidden;
    background: var(--backdrop);
    font-family: "Open Sans", Arial, sans-serif;
  }
  .stage { position: relative; width: 1200px; height: 900px; }

  .card { position: absolute; top: 200px; width: 310px; height: 500px; }
  .card-front {
    left: 265px; background: var(--card-white);
    border-radius: 48px 0 48px 0;
  }
  .card-back {
    left: 640px; background: var(--brand-orange);
    border-radius: 0 48px 0 48px;
  }

  .brand-square { position: absolute; }
  .card-front .brand-square {
    left: 131px; top: 36px; width: 88px; height: 88px;
    background: var(--brand-orange);
  }
  .card-back .brand-square {
    left: 101px; top: 280px; width: 99px; height: 99px;
    background: var(--mark-white);
  }

  .brand-name {
    position: absolute; font-weight: 400; line-height: 1.05; text-align: right;
  }
  .card-front .brand-name {
    right: 36px; top: 146px; width: 260px;
    font-size: 25px; color: var(--brand-orange);
  }
  .card-back .brand-name {
    left: 20px; right: 20px; top: 400px; text-align: center;
    font-size: 27px; color: var(--mark-white);
  }

  .holder { position: absolute; left: 28px; top: 268px; }
  .holder-name { font-size: 17px; font-weight: 600; color: var(--brand-orange); }
  .holder-role { font-size: 13.5px; color: var(--text-dark); margin-top: 1px; }

  .address {
    position: absolute; left: 22px; top: 331px;
    font-size: 13.5px; line-height: 21px; color: var(--text-dark); font-style: normal;
  }

  .contact-list { position: absolute; left: 22px; top: 395px; list-style: none; }
  .contact-item {
    display: flex; align-items: center; gap: 7px;
    font-size: 13.5px; line-height: 21px; color: var(--text-dark);
  }
  .contact-icon { width: 11px; height: 11px; fill: var(--brand-orange); }

  .registration {
    position: absolute; left: 22px; top: 450px;
    font-size: 13px; font-weight: 600; color: var(--brand-orange);
  }
</style>
</head>
<body>
<main class="stage">
  <section class="card card-front" aria-label="Card front">
    <div class="brand-square"></div>
    <div class="brand-name">Brevora Technologies</div>

    <div class="holder">
      <p class="holder-name">Adrian Teo</p>
      <p class="holder-role">Founder, Managing Director</p>
    </div>

    <address class="address">
      47 Merrow Street, Calder House,<br>
      #14-03 Singapore 068215
    </address>

    <ul class="contact-list">
      <li class="contact-item">
        <svg class="contact-icon" viewBox="0 0 24 24" aria-hidden="true">
          <path d="M6.6 10.8a15.1 15.1 0 0 0 6.6 6.6l2.2-2.2c.3-.3.7-.4 1-.2 1.1.4 2.3.6 3.6.6.6 0 1 .4 1 1V20c0 .6-.4 1-1 1A17 17 0 0 1 3 4c0-.6.4-1 1-1h3.5c.6 0 1 .4 1 1 0 1.3.2 2.5.6 3.6.1.3 0 .7-.2 1z"/>
        </svg>
        +65 98471360
      </li>
      <li class="contact-item">
        <svg class="contact-icon" viewBox="0 0 24 24" aria-hidden="true">
          <path d="M2 5h20v14H2z M2 5l10 7 10-7" />
        </svg>
        adrian.t@brevoratech.com
      </li>
    </ul>

    <p class="registration">Company Registration no. 201678213K</p>
  </section>

  <section class="card card-back" aria-label="Card back">
    <div class="brand-square"></div>
    <div class="brand-name">Brevora Technologies</div>
  </section>
</main>
</body>
</html>
```